Ductless Mini Split Business Website

Copper Fern Services is looking to design an eye catching educational website about installing Ductless mini splits.

Similar to this company.
https://www.halvikstream.com/

Coding

Coded - Design and coding required

```html
<!DOCTYPE html>
<html lang="en">
<head>
<meta charset="utf-8">
<title>Copper Fern Services – Ductless Experts</title>
<link rel="stylesheet" href="https://fonts.googleapis.com/css2?family=Oswald:wght@400;500;600;700&family=Open+Sans:wght@400;600;700&family=Playfair+Display:wght@700&display=swap">
<style>
:root{
  --yellow:#fdd20a;
  --black:#111111;
  --dark:#1c1c1c;
  --ink:#222222;
  --muted:#777777;
  --light:#f4f4f4;
  --white:#ffffff;
  --line:#e3e3e3;
}
*{box-sizing:border-box;margin:0;padding:0}
html,body{width:1200px;height:4628px;overflow:hidden}
body{font-family:"Open Sans",Arial,sans-serif;color:var(--ink);background:var(--white);position:relative}
.abs{position:absolute}
h1,h2,h3,.oswald{font-family:"Oswald","Arial Narrow",sans-serif;font-weight:600}
.btn{display:inline-block;font-family:"Oswald",sans-serif;font-size:15px;letter-spacing:.5px;text-transform:uppercase;padding:12px 24px;font-weight:500}
.btn-yellow{background:var(--yellow);color:var(--black)}
.btn-white{background:var(--white);color:var(--black)}
.btn-black{background:var(--black);color:var(--white)}
.btn-outline{border:2px solid var(--white);color:var(--white)}

/* top bar */
.topbar{top:0;left:0;width:1200px;height:32px;background:var(--black);color:var(--white);font-size:13px;display:flex;align-items:center;padding:0 40px;justify-content:space-between}
.topbar .right{display:flex;align-items:center;gap:14px}
.topbar .dot{width:14px;height:14px;border-radius:50%;background:#555;display:inline-block}
.topbar .call{background:var(--yellow);color:var(--black);height:32px;display:flex;align-items:center;padding:0 18px;font-weight:700}

/* header */
.header{top:32px;left:0;width:1200px;height:120px;display:flex;align-items:center;justify-content:space-between;padding:0 60px}
.brand{display:flex;align-items:center;gap:12px;font-family:"Oswald",sans-serif;font-weight:600;font-size:26px;color:var(--black)}
.brand .mark{width:30px;height:30px;border-radius:50%;background:var(--yellow)}
.nav{display:flex;gap:34px;font-family:"Oswald",sans-serif;font-size:15px;text-transform:uppercase}
.nav .active{border-bottom:3px solid var(--yellow);padding-bottom:4px}

/* hero */
.hero{top:152px;left:0;width:1200px;height:720px;background:linear-gradient(100deg,#5c6470 0%,#9aa1a8 45%,#cfd3d6 100%)}
.hero-title{top:236px;left:64px;color:var(--white);font-size:86px;line-height:88px;text-transform:uppercase}
.hero-sub{top:432px;left:64px;color:var(--white);font-size:22px;font-weight:600}
.hero-phone{top:466px;left:64px;color:var(--white);font-size:22px;font-weight:700}
.hero-btns{top:536px;left:64px;display:flex;gap:20px}
.hero-arrow{width:48px;height:48px;border-radius:50%;background:var(--white);display:flex;align-items:center;justify-content:center}

/* features */
.features{top:800px;left:104px;width:992px;height:360px;display:flex;gap:0;background:var(--white);box-shadow:0 6px 28px rgba(0,0,0,.12)}
.feature{flex:1;text-align:center;padding:36px 30px;border-right:1px solid var(--line);position:relative}
.feature:last-child{border-right:0}
.feature .icon{width:120px;height:120px;border-radius:50%;background:var(--yellow);margin:0 auto 28px;display:flex;align-items:center;justify-content:center}
.feature h3{font-size:17px;text-transform:uppercase;margin-bottom:12px}
.feature p{font-size:13px;color:var(--muted);line-height:20px}
.feature .more{width:34px;height:34px;border-radius:50%;border:1px solid var(--line);margin:22px auto 0;display:flex;align-items:center;justify-content:center}

/* services */
.section-title{left:0;width:1200px;text-align:center;font-size:40px;text-transform:uppercase;color:var(--black)}
.services{top:1312px;left:88px;width:1024px;display:flex;gap:10px}
.service{width:248px;height:328px;position:relative}
.service span{position:absolute;bottom:18px;left:0;width:100%;text-align:center;color:var(--white);font-family:"Oswald",sans-serif;font-size:15px;text-transform:uppercase;line-height:19px}

/* about */
.about{top:1840px;left:0;width:612px;height:560px;background:var(--black);color:var(--white);padding:120px 60px 0 84px}
.about .bar{position:absolute;left:64px;top:120px;width:5px;height:98px;background:var(--yellow)}
.about small{font-size:13px;text-transform:uppercase;letter-spacing:1px}
.about h2{font-size:44px;line-height:50px;text-transform:uppercase;margin-top:6px}
.about p{font-size:14px;line-height:22px;color:#cccccc;margin:32px 0 30px -20px;width:480px}
.about-photo{top:1820px;left:612px;width:588px;height:580px;background:linear-gradient(135deg,#d9d4cd,#b8aea3 55%,#e58a3a)}
.play{top:2050px;left:852px;width:100px;height:100px;border-radius:50%;background:var(--white);display:flex;align-items:center;justify-content:center}

/* contact */
.contact{top:2400px;left:0;width:1200px;height:600px;background:var(--yellow)}
.contact-portrait{top:2480px;left:60px;width:300px;height:380px}
.contact-portrait .disc{position:absolute;left:0;top:80px;width:300px;height:300px;border-radius:50%;background:linear-gradient(160deg,#e7e2dc,#c77d3c 60%,#7a5030)}
.contact-portrait .tag{position:absolute;left:40px;top:270px;width:220px;background:var(--white);padding:10px 12px;text-align:center;font-family:"Oswald",sans-serif;font-size:18px;font-weight:600}
.contact-form{top:2508px;left:544px;width:526px}
.contact-form h2{font-family:"Playfair Display",Georgia,serif;font-size:34px;color:var(--black);text-transform:uppercase;margin-bottom:18px}
.row{display:flex;gap:12px;margin-bottom:12px}
.field{flex:1;height:44px;background:var(--white);font-size:11px;padding:14px 12px;font-weight:700;text-transform:uppercase}
.field.select{font-weight:400;text-transform:none;color:#888}
.field.msg{height:104px}

/* stand behind */
.cards{top:3280px;left:88px;width:1024px;display:flex;gap:16px}
.card{flex:1;background:var(--white);box-shadow:0 4px 20px rgba(0,0,0,.12);text-align:center}
.card .ph{height:200px}
.card h3{font-family:"Oswald",sans-serif;font-weight:500;font-size:24px;text-transform:uppercase;margin:28px 0 18px}
.card .btn{font-size:12px;padding:9px 18px;margin-bottom:28px}

/* testimonial */
.avatars{top:3732px;left:0;width:1200px;display:flex;justify-content:center;align-items:center;gap:22px}
.avatar{width:44px;height:44px;border-radius:50%;background:linear-gradient(135deg,#c8bfb5,#8a7c70)}
.avatar.main{width:84px;height:84px;border:4px solid var(--yellow)}
.quote{top:3830px;left:290px;width:620px;text-align:center;font-size:15px;line-height:24px;color:#555;font-style:italic}
.qmark{font-family:"Playfair Display",serif;font-size:90px;color:var(--yellow);line-height:1}
.author{top:3906px;left:0;width:1200px;text-align:center;font-size:13px;color:#c29f00;font-weight:700}

/* perks band */
.perks{top:4028px;left:0;width:1200px;height:180px;background:var(--yellow);display:flex;justify-content:center;align-items:center;gap:130px}
.perk{display:flex;align-items:center;gap:18px;font-family:"Oswald",sans-serif;font-size:20px;text-transform:uppercase;color:var(--black)}
.perk .ring{width:78px;height:78px;border-radius:50%;background:var(--white);display:flex;align-items:center;justify-content:center}

/* footer */
.footer{top:4208px;left:0;width:1200px;height:372px;background:var(--black);color:var(--white)}
.footer .brand{position:absolute;left:88px;top:150px;color:var(--yellow)}
.fcol{position:absolute;top:56px}
.fcol h4{font-family:"Oswald",sans-serif;color:var(--yellow);text-transform:uppercase;font-size:16px;font-weight:500;margin-bottom:20px}
.fcol li{list-style:none;font-size:13px;line-height:26px;color:#dddddd}
.fcol p{font-size:13px;line-height:22px;color:#dddddd}
.subscribe{display:flex;margin-top:16px}
.subscribe div{width:220px;height:40px;background:var(--white);border-radius:20px 0 0 20px;color:#888;font-size:12px;padding:12px 16px}
.subscribe span{width:44px;height:40px;background:var(--yellow);border-radius:0 20px 20px 0}
.social{display:flex;gap:10px;margin-top:20px}
.social i{width:30px;height:30px;border-radius:50%;background:#3a3a3a;display:block}
.copy{top:4580px;left:0;width:1200px;height:48px;background:#000;color:#aaaaaa;font-size:12px;text-align:center;line-height:48px;border-top:1px solid #333}
</style>
</head>
<body>

<div class="abs topbar">
  <div>&#9679; 24/7 Emergency Service Available</div>
  <div class="right">
    <span class="dot"></span><span class="dot"></span><span class="dot"></span><span class="dot"></span>
    <span class="call">Call us (555) 014-2287</span>
  </div>
</div>

<header class="abs header">
  <div class="brand"><span class="mark"></span>Copper Fern Services</div>
  <nav class="nav">
    <span class="active">About</span><span>Ductless Heat Pumps</span><span>Ductless Heat Pumps FAQ</span><span>Financing</span><span>Reviews</span><span>Contact</span>
  </nav>
</header>

<section class="abs hero" role="img" aria-label="Living room with a wall-mounted ductless unit, sofa and potted plant"></section>
<h1 class="abs hero-title">Ductless<br>Does It Better</h1>
<div class="abs hero-sub">Let Ductless Experts Show You How</div>
<div class="abs hero-phone">(555) 014-2287</div>
<div class="abs hero-btns"><span class="btn btn-white">Get Services Now</span><span class="btn btn-yellow">Request an Estimate</span></div>
<div class="abs hero-arrow" style="top:428px;left:20px"><svg width="16" height="16" viewBox="0 0 16 16"><path d="M10 3 5 8l5 5" stroke="#111" stroke-width="2" fill="none"/></svg></div>
<div class="abs hero-arrow" style="top:428px;left:1092px"><svg width="16" height="16" viewBox="0 0 16 16"><path d="M6 3l5 5-5 5" stroke="#111" stroke-width="2" fill="none"/></svg></div>

<div class="abs features">
  <div class="feature">
    <div class="icon"><svg width="56" height="56" viewBox="0 0 56 56" fill="none" stroke="#111" stroke-width="3"><rect x="12" y="8" width="32" height="40" rx="3"/><circle cx="22" cy="22" r="4"/><circle cx="34" cy="36" r="4"/><path d="M36 18 20 40"/></svg></div>
    <h3>0% Financing for 60 Months</h3>
    <p>Flexible monthly plans make a new ductless system easy to fit into any home budget.</p>
    <div class="more"><svg width="12" height="12" viewBox="0 0 12 12"><path d="M4 2l4 4-4 4" stroke="#111" stroke-width="1.6" fill="none"/></svg></div>
  </div>
  <div class="feature">
    <div class="icon"><svg width="56" height="56" viewBox="0 0 56 56" fill="none" stroke="#111" stroke-width="3"><path d="M8 28a20 20 0 0 1 40 0z"/><path d="M28 28v16a4 4 0 0 1-8 0"/><path d="M28 8v-2"/></svg></div>
    <h3>365 Day Money Back Guarantee</h3>
    <p>If you are not happy in the first year, we will make it right or refund your money.</p>
    <div class="more"><svg width="12" height="12" viewBox="0 0 12 12"><path d="M4 2l4 4-4 4" stroke="#111" stroke-width="1.6" fill="none"/></svg></div>
  </div>
  <div class="feature">
    <div class="icon"><svg width="56" height="56" viewBox="0 0 56 56" fill="none" stroke="#111" stroke-width="3"><circle cx="24" cy="20" r="9"/><path d="M8 48c2-10 9-15 16-15s10 2 12 5"/><circle cx="40" cy="42" r="7"/><path d="M45 47l5 5"/></svg></div>
    <h3>We Are the Experts in Ductless</h3>
    <p>Certified installers with years of hands-on mini split work across the region.</p>
    <div class="more"><svg width="12" height="12" viewBox="0 0 12 12"><path d="M4 2l4 4-4 4" stroke="#111" stroke-width="1.6" fill="none"/></svg></div>
  </div>
</div>

<h2 class="abs section-title" style="top:1244px">How Can We Help You?</h2>
<div class="abs services">
  <div class="service" role="img" aria-label="Technician servicing an indoor ductless unit" style="background:linear-gradient(180deg,#8a9097,#2d3033)"><span>Ductless<br>Maintenance</span></div>
  <div class="service" role="img" aria-label="Open ductless unit with filters being repaired" style="background:linear-gradient(180deg,#b9bcbf,#3c3f42)"><span>Ductless<br>Repairs</span></div>
  <div class="service" role="img" aria-label="Hand holding a remote below a wall unit" style="background:linear-gradient(180deg,#d4d2cf,#5a5652)"><span>Ductless<br>Warranty</span></div>
  <div class="service" role="img" aria-label="Installer in an orange cap fitting a wall unit" style="background:linear-gradient(180deg,#d5d0c9,#c4692c 70%,#4a3020)"><span>Ductless<br>Installation</span></div>
</div>
<div class="abs" style="top:1668px;left:0;width:1200px;text-align:center"><span class="btn btn-yellow">More Ductless Services</span></div>

<section class="abs about">
  <span class="bar"></span>
  <small>About Us</small>
  <h2>Introduction<br>Copper Fern Services</h2>
  <p>We install, tune and repair ductless mini splits for homes and small offices. Our crews arrive on time, explain every option clearly and leave each room cleaner than they found it. Ask us anything about efficiency, rebates and comfort.</p>
  <span class="btn btn-outline">Learn More</span>
</section>
<div class="abs about-photo" role="img" aria-label="Smiling installer in an orange cap next to an indoor unit"></div>
<div class="abs play"><svg width="30" height="30" viewBox="0 0 30 30"><path d="M9 5l16 10-16 10z" fill="#111"/></svg></div>

<section class="abs contact"></section>
<div class="abs contact-portrait">
  <div class="disc" role="img" aria-label="Installer in a hard hat and plaid shirt"></div>
  <div class="tag">Copper Fern Services</div>
</div>
<div class="abs contact-form">
  <h2>Contact Us Today</h2>
  <div class="row"><div class="field">First Name*</div><div class="field">Last Name*</div></div>
  <div class="row"><div class="field">Email*</div><div class="field">Phone*</div></div>
  <div class="row"><div class="field select">Are you a new customer ▾</div></div>
  <div class="row"><div class="field msg">Message*</div></div>
  <span class="btn btn-black" style="margin-top:8px">More Ductless Services</span>
</div>

<h2 class="abs section-title" style="top:3092px">We Stand Behind Our Ductless Services</h2>
<div class="abs cards">
  <div class="card"><div class="ph" role="img" aria-label="Hand adjusting a wall unit" style="background:linear-gradient(135deg,#eef0f2,#aab2ba)"></div><h3>Get Some Answers</h3><span class="btn btn-yellow">Ductless FAQ</span></div>
  <div class="card"><div class="ph" role="img" aria-label="Hands counting cash" style="background:linear-gradient(135deg,#8a8266,#3d3a2c)"></div><h3>Our Financing Options</h3><span class="btn btn-yellow">Financing</span></div>
  <div class="card"><div class="ph" role="img" aria-label="Remote pointed at a wall unit" style="background:linear-gradient(135deg,#f3f3f3,#b9bcbf)"></div><h3>Stay Up To Date</h3><span class="btn btn-yellow">Our Blog</span></div>
</div>

<h2 class="abs section-title" style="top:3648px;font-size:36px">Client's Testimonial</h2>
<div class="abs avatars" role="img" aria-label="Client portraits">
  <span class="avatar"></span><span class="avatar"></span><span class="avatar main"></span><span class="avatar"></span><span class="avatar"></span>
</div>
<div class="abs qmark" style="top:3820px;left:220px">&ldquo;</div>
<p class="abs quote">The crew explained every step, finished the install in one day, and our upstairs finally stays cool all summer long.</p>
<div class="abs qmark" style="top:3860px;left:920px">&rdquo;</div>
<div class="abs author">Dana Whitfield</div>

<section class="abs perks">
  <div class="perk"><span class="ring"><svg width="40" height="40" viewBox="0 0 40 40" fill="none" stroke="#111" stroke-width="2.5"><circle cx="20" cy="20" r="15"/><text x="20" y="25" font-size="13" text-anchor="middle" fill="#111" stroke="none" font-family="Oswald">24</text></svg></span>Available 24/7</div>
  <div class="perk"><span class="ring"><svg width="42" height="30" viewBox="0 0 42 30" fill="none" stroke="#111" stroke-width="2.5"><path d="M2 5h24v16H2zM26 11h8l6 6v4h-14"/><circle cx="10" cy="24" r="4"/><circle cx="32" cy="24" r="4"/></svg></span>Speedy Service</div>
  <div class="perk"><span class="ring"><svg width="42" height="30" viewBox="0 0 42 30" fill="none" stroke="#111" stroke-width="2.5"><path d="M3 12l8-7 8 5 8-5 12 7M6 14l12 11 4-3 4 3 10-11"/></svg></span>Friendly Service</div>
</section>

<footer class="abs footer">
  <div class="brand"><span class="mark"></span>Copper Fern Services</div>
  <div class="fcol" style="left:380px"><h4>Quick Links</h4>
    <ul><li>Home</li><li>About Us</li><li>Ductless Heat Pumps</li><li>Ductless Heat Pumps FAQ</li><li>Financing</li><li>Contact Us</li></ul></div>
  <div class="fcol" style="left:592px"><h4>Contact Info</h4>
    <p>Email<br>hello@copperfern.example</p><p style="margin-top:10px">Phone<br>(555) 014-2287</p><p style="margin-top:10px">Office Location<br>Some address line goes here</p></div>
  <div class="fcol" style="left:848px"><h4>Newsletter</h4>
    <p>Subscribe to our email address to<br>get the latest news.</p>
    <div class="subscribe"><div>Enter Your Email</div><span></span></div>
    <div class="social"><i></i><i></i><i></i><i></i></div></div>
</footer>
<div class="abs copy">&copy; Copyright 2019 &nbsp;|&nbsp; All Rights Reserved</div>

</body>
</html>
```